Real Estate Company Looking for Business Card Designs for 3 Executives

Hello!
Thanks so much for considering our project! We are a real estate investment company located in Edmonton, Alberta called Bellhaven Group of Companies. We invest/develop both commercial and residential real estate and are looking to create 3 DOUBLE-SIDED business cards for 3 top executives in the company! (for some reason it won't let us select the double-sided option, but yes, the cards are double sided and would be happy to tip extra)

We have certain guidelines that we want our business cards to for sure follow - the back of the Business card has to be the Black Background Version of the Logo which has already been designed and linked as a file (first file). We want the entire back of the card to simply just be the black background logo. In terms of the front of the card, would like to see a smaller version of the white background logo (linked as the second file) in the top left hand corner - of course, feel free to get creative and we can make revisions together along the way! and Then after that, just text. We want the card to be sharp, clean, easy on the eyes and highly professional looking. We would like the card to include the Full name of the Company (Bellhaven Group of Companies), Name of the Person, Title, Phone, Email. If possible please provide the front part of the card for 3 people:

1) Bellhaven Group of Companies, Liora Quenby, Chief Financial Officer, 780-555-0142, lioraquenby@bellhavengroup.example

2) Bellhaven Group of Companies, Tobias Quenby, Chief Executive Officer, 780-555-0187, tobiasquenby@bellhavengroup.example

3) Bellhaven Group of Companies, Rui Delcourt, Chief Operations Officer, 587-555-0163, ruidelcourt@bellhavengroup.example

Thank you so much for considering our project & we look forward to seeing your designs!

```html
<!DOCTYPE html>
<html lang="en">
<head>
<meta charset="utf-8">
<title>Bellhaven Group of Companies – Executive Business Cards</title>
<link rel="stylesheet" href="https://fonts.googleapis.com/css2?family=Arimo:wght@400;700&family=Tinos:wght@700&display=swap">
<style>
  :root {
    --backdrop: #d2d4d5;
    --card-white: #f3f3f1;
    --card-black: #0c0c0c;
    --ink: #111111;
    --ink-soft: #2a2a2a;
    --paper-text: #f1f1f1;
    --rule: #3a3a3a;
  }
  * { box-sizing: border-box; margin: 0; padding: 0; }
  html, body {
    width: 1200px;
    height: 2679px;
    overflow: hidden;
    background: var(--backdrop);
  }
  .sheet {
    width: 1200px;
    height: 2679px;
    display: grid;
    grid-template-rows: repeat(3, 1fr);
  }
  .card-set {
    display: flex;
    align-items: center;
    justify-content: center;
    gap: 40px;
  }
  .card {
    width: 540px;
    height: 310px;
    position: relative;
    box-shadow: 0 6px 18px rgba(0,0,0,0.18);
  }
  .card-front { background: var(--card-white); color: var(--ink); }
  .card-back {
    background: var(--card-black);
    display: flex;
    align-items: center;
    justify-content: center;
  }

  .brand {
    position: absolute;
    left: 32px;
    top: 96px;
    width: 180px;
    font-family: "Arimo", sans-serif;
    font-weight: 400;
    font-size: 15px;
    letter-spacing: 0.18em;
    text-transform: uppercase;
    line-height: 1.6;
    color: var(--ink);
  }
  .brand-name { display: block; font-size: 22px; letter-spacing: 0.2em; }
  .brand-sub { display: block; font-size: 10.5px; letter-spacing: 0.16em; }

  .divider {
    position: absolute;
    left: 228px;
    top: 70px;
    width: 1px;
    height: 170px;
    background: var(--rule);
  }

  .details {
    position: absolute;
    left: 248px;
    top: 92px;
    right: 16px;
    font-family: "Arimo", sans-serif;
    color: var(--ink);
  }
  .person-name {
    font-family: "Tinos", serif;
    font-weight: 700;
    font-size: 20px;
    text-transform: uppercase;
    letter-spacing: 0.01em;
  }
  .person-title {
    font-size: 14px;
    color: var(--ink-soft);
    margin-top: 2px;
    margin-bottom: 12px;
  }
  .contact-list { list-style: none; }
  .contact-list li {
    display: flex;
    align-items: center;
    gap: 7px;
    font-size: 13px;
    line-height: 1.75;
    white-space: nowrap;
  }
  .contact-list svg { width: 11px; height: 11px; flex: none; fill: var(--ink); }

  .back-brand {
    text-align: center;
    font-family: "Arimo", sans-serif;
    font-weight: 400;
    color: var(--paper-text);
    text-transform: uppercase;
    line-height: 1.7;
  }
  .back-brand .brand-name { font-size: 34px; letter-spacing: 0.24em; }
  .back-brand .brand-sub { font-size: 14px; letter-spacing: 0.2em; }
</style>
</head>
<body>
<svg width="0" height="0" style="position:absolute" aria-hidden="true">
  <defs>
    <symbol id="icon-phone" viewBox="0 0 24 24"><path d="M6.6 10.8a15.1 15.1 0 0 0 6.6 6.6l2.2-2.2a1 1 0 0 1 1-.25 11.4 11.4 0 0 0 3.6.57 1 1 0 0 1 1 1V20a1 1 0 0 1-1 1A17 17 0 0 1 3 4a1 1 0 0 1 1-1h3.5a1 1 0 0 1 1 1c0 1.25.2 2.45.57 3.57a1 1 0 0 1-.25 1z"/></symbol>
    <symbol id="icon-mail" viewBox="0 0 24 24"><path d="M2 5h20v14H2z M3.5 6.5 12 13l8.5-6.5" fill-rule="evenodd"/><path d="M2 5l10 8 10-8v-.01H2z" fill="#fff" opacity=".9"/></symbol>
    <symbol id="icon-globe" viewBox="0 0 24 24"><circle cx="12" cy="12" r="10"/><path d="M2 12h20M12 2c3 3 3 17 0 20M12 2c-3 3-3 17 0 20" stroke="#fff" stroke-width="1.4" fill="none"/></symbol>
  </defs>
</svg>

<main class="sheet">
  <section class="card-set">
    <article class="card card-front">
      <div class="brand"><span class="brand-name">Bellhaven</span><span class="brand-sub">Group of Companies</span></div>
      <div class="divider"></div>
      <div class="details">
        <h2 class="person-name">Tobias Quenby</h2>
        <p class="person-title">Chief Executive Officer</p>
        <ul class="contact-list">
          <li><svg><use href="#icon-phone"/></svg>780-555-0187</li>
          <li><svg><use href="#icon-mail"/></svg>tobiasquenby@bellhavengroup.example</li>
          <li><svg><use href="#icon-globe"/></svg>www.bellhavengroup.example</li>
        </ul>
      </div>
    </article>
    <article class="card card-back">
      <div class="back-brand"><span class="brand-name">Bellhaven</span><span class="brand-sub">Group of Companies</span></div>
    </article>
  </section>

  <section class="card-set">
    <article class="card card-front">
      <div class="brand"><span class="brand-name">Bellhaven</span><span class="brand-sub">Group of Companies</span></div>
      <div class="divider"></div>
      <div class="details">
        <h2 class="person-name">Liora Quenby</h2>
        <p class="person-title">Chief Financial Officer</p>
        <ul class="contact-list">
          <li><svg><use href="#icon-phone"/></svg>780-555-0142</li>
          <li><svg><use href="#icon-mail"/></svg>lioraquenby@bellhavengroup.example</li>
          <li><svg><use href="#icon-globe"/></svg>www.bellhavengroup.example</li>
        </ul>
      </div>
    </article>
    <article class="card card-back">
      <div class="back-brand"><span class="brand-name">Bellhaven</span><span class="brand-sub">Group of Companies</span></div>
    </article>
  </section>

  <section class="card-set">
    <article class="card card-front">
      <div class="brand"><span class="brand-name">Bellhaven</span><span class="brand-sub">Group of Companies</span></div>
      <div class="divider"></div>
      <div class="details">
        <h2 class="person-name">Rui Delcourt</h2>
        <p class="person-title">Chief Operations Officer</p>
        <ul class="contact-list">
          <li><svg><use href="#icon-phone"/></svg>587-555-0163</li>
          <li><svg><use href="#icon-mail"/></svg>ruidelcourt@bellhavengroup.example</li>
          <li><svg><use href="#icon-globe"/></svg>www.bellhavengroup.example</li>
        </ul>
      </div>
    </article>
    <article class="card card-back">
      <div class="back-brand"><span class="brand-name">Bellhaven</span><span class="brand-sub">Group of Companies</span></div>
    </article>
  </section>
</main>
</body>
</html>
```